SkyvornQ Business Cards and Stationary Design

Need a design for our business cards and stationary. I want to carry on the theme of the logo. I want the business cards to have a design on the back. I would like the business cards and the stationary to carry the same theme, design scheme, and branding

Target Market(s)

Airlines and Maintenance Facilities

Industry/Entity Type

Aviation

Contact Information for Business Card

Name
Position Title
Address: 4827 Trellis Hollow Road, Brennick Falls, Ohio, 34951
Office Number
Mobile Number
Email
Website

Font styles to use
Serif
Sans Serif

Colors

Designer to choose colors to be used in the design.

```html
<!DOCTYPE html>
<html lang="en">
<head>
<meta charset="utf-8">
<title>SkyvornQ Business Card</title>
<link href="https://fonts.googleapis.com/css2?family=Roboto:wght@400;500;700;900&display=swap" rel="stylesheet">
<style>
  :root {
    --page-bg: #e9e7e3;
    --card-bg: #f7f7f7;
    --navy: #1c2d52;
    --brand-blue: #1b5fae;
    --sky-blue: #2a8fd8;
    --text-grey: #4a4f58;
    --band-dark: #123f86;
    --band-light: #2d7fd0;
  }
  * { margin: 0; padding: 0; box-sizing: border-box; }
  html, body { width: 1200px; height: 911px; overflow: hidden; }
  body {
    background: var(--page-bg);
    font-family: "Roboto", sans-serif;
    position: relative;
  }
  .card {
    position: absolute;
    top: 165px;
    width: 340px;
    height: 580px;
    background: var(--card-bg);
    border-radius: 22px;
    box-shadow: 0 6px 18px rgba(0,0,0,0.12);
    overflow: hidden;
  }
  .card-front { left: 190px; }
  .card-back { left: 670px; }

  /* Front */
  .brand {
    position: absolute;
    top: 70px;
    left: 0; right: 0;
    text-align: center;
  }
  .brand-mark {
    width: 60px; height: 60px;
    margin: 0 auto 14px;
    border: 6px solid var(--brand-blue);
    border-radius: 50%;
  }
  .brand-name {
    color: var(--navy);
    font-weight: 900;
    font-size: 30px;
    letter-spacing: 6px;
    padding-left: 6px;
  }
  .person {
    position: absolute;
    top: 215px;
    left: 0; right: 0;
    text-align: center;
  }
  .person-name {
    color: var(--navy);
    font-weight: 700;
    font-size: 20px;
    letter-spacing: 1px;
  }
  .person-title {
    color: var(--sky-blue);
    font-weight: 500;
    font-size: 14px;
    letter-spacing: 1px;
    margin-top: 2px;
  }
  .divider {
    position: absolute;
    left: 40px;
    width: 260px;
    height: 24px;
  }
  .divider-address { top: 282px; }
  .divider-contact { top: 380px; }
  .address, .contacts {
    position: absolute;
    left: 0; right: 0;
    text-align: center;
    color: var(--text-grey);
    font-size: 14px;
    line-height: 19px;
  }
  .address { top: 316px; }
  .contacts { top: 414px; }

  /* Back */
  .back-brand {
    position: absolute;
    top: 220px;
    left: 0; right: 0;
    text-align: center;
  }
  .back-brand .brand-mark {
    width: 120px; height: 120px;
    border-width: 10px;
    margin-bottom: 20px;
  }
  .back-brand .brand-name { font-size: 30px; }
  .web-band {
    position: absolute;
    left: 0; right: 0;
    top: 478px;
    height: 42px;
    background: linear-gradient(90deg, var(--band-dark), var(--band-light) 70%, var(--band-dark));
    color: #fff;
    font-size: 13px;
    letter-spacing: 5px;
    text-align: center;
    line-height: 42px;
  }
</style>
</head>
<body>
  <section class="card card-front">
    <div class="brand">
      <div class="brand-mark"></div>
      <div class="brand-name">SKYVORNQ</div>
    </div>

    <div class="person">
      <div class="person-name">DORIAN VALE</div>
      <div class="person-title">CEO/FOUNDER</div>
    </div>

    <svg class="divider divider-address" viewBox="0 0 260 24" aria-hidden="true">
      <line x1="0" y1="12" x2="118" y2="12" stroke="var(--sky-blue)" stroke-width="1.2"/>
      <line x1="142" y1="12" x2="260" y2="12" stroke="var(--navy)" stroke-width="1.2"/>
      <circle cx="130" cy="12" r="10" fill="none" stroke="var(--brand-blue)" stroke-width="1.5"/>
      <path d="M130 18 C126 13 125.5 11.5 125.5 10 A4.5 4.5 0 0 1 134.5 10 C134.5 11.5 134 13 130 18Z" fill="var(--navy)"/>
      <circle cx="130" cy="10" r="1.6" fill="#fff"/>
    </svg>

    <div class="address">
      4827 Trellis Hollow Road<br>
      Brennick Falls, Ohio, 34951
    </div>

    <svg class="divider divider-contact" viewBox="0 0 260 24" aria-hidden="true">
      <line x1="0" y1="12" x2="82" y2="12" stroke="var(--sky-blue)" stroke-width="1.2"/>
      <line x1="178" y1="12" x2="260" y2="12" stroke="var(--navy)" stroke-width="1.2"/>
      <g fill="none" stroke="var(--brand-blue)" stroke-width="1.5">
        <circle cx="94" cy="12" r="10"/>
        <circle cx="118" cy="12" r="10"/>
        <circle cx="142" cy="12" r="10"/>
        <circle cx="166" cy="12" r="10"/>
      </g>
      <path d="M90 7 l2.5 -1 l1.5 3 l-1.5 1.2 q1 2.5 3.3 3.3 l1.2 -1.5 l3 1.5 l-1 2.5 q-6 0 -9 -9Z" fill="var(--navy)"/>
      <rect x="114.5" y="6" width="7" height="12" rx="1.2" fill="none" stroke="var(--navy)" stroke-width="1.4"/>
      <rect x="136.5" y="8" width="11" height="8" rx="1" fill="var(--navy)"/>
      <path d="M136.5 8 l5.5 4.5 l5.5 -4.5" fill="none" stroke="#fff" stroke-width="1"/>
      <circle cx="166" cy="12" r="5.5" fill="none" stroke="var(--navy)" stroke-width="1.3"/>
      <line x1="160.5" y1="12" x2="171.5" y2="12" stroke="var(--navy)" stroke-width="1"/>
      <ellipse cx="166" cy="12" rx="2.4" ry="5.5" fill="none" stroke="var(--navy)" stroke-width="1"/>
    </svg>

    <div class="contacts">
      772 555 0148<br>
      772 555 0193<br>
      info@skyvornq.com<br>
      info@skyvornq.com
    </div>
  </section>

  <section class="card card-back">
    <div class="back-brand">
      <div class="brand-mark"></div>
      <div class="brand-name">SKYVORNQ</div>
    </div>
    <div class="web-band">www.skyvornq.com</div>
  </section>
</body>
</html>
```